Heron Haulage needs Bussiness cards!

Our new trucking company needs business cards!
We need the same design with two different names and emails, everything else it's the same.
I have included our original logo so we can use it for the design.
Note: the logo to be used is the o e with the buffalo on the right side, next to the letters H and H.

Target Market(s)

Trucking, refrigerated transportation, freight

Industry/Entity Type

Business

Contact Information for Business Card

Card #1:
Marcus Whitfield
marcuswhitfield@heronhaulage.example
1-855-317-6094
(956)238-7160
4117 W. Larkin Ave.
Pharr, TX 78590
www.heronhaulage.example

Card#2:
Rosalba Quintero
rosalba@heronhaulage.example
1-855-317-6094
(956)238-7160
4117 W. Larkin Ave.
Pharr, TX 78590
www.heronhaulage.example

Font styles to use
Sans Serif

Colors
0655a3
ec1f27
ffffff

Requirements
Must have
• our logo
Nice to have
• roads on background,

```html
<!DOCTYPE html>
<html lang="en">
<head>
<meta charset="utf-8">
<title>Heron Haulage — Business Cards</title>
<link rel="stylesheet" href="https://fonts.googleapis.com/css2?family=Source+Sans+3:wght@400;600;700&display=swap">
<style>
  :root {
    --brand-blue: #0655a3;
    --brand-red: #ec1f27;
    --white: #ffffff;
    --card-black: #1b1b1d;
    --stage: #2a2a2c;
    --rule: #3a3a3e;
    --text-soft: #e9e9ea;
  }
  * { box-sizing: border-box; margin: 0; padding: 0; }
  html, body {
    width: 1200px;
    height: 900px;
    overflow: hidden;
    background: var(--stage);
    font-family: "Source Sans 3", "Helvetica Neue", Arial, sans-serif;
  }
  .card-set {
    position: absolute;
    inset: 0;
    display: flex;
    align-items: center;
    justify-content: center;
    gap: 40px;
  }
  .card {
    position: relative;
    width: 520px;
    height: 300px;
    border-radius: 22px;
    background: var(--card-black);
    overflow: hidden;
  }
  /* Front: mascot artwork + contact details */
  .mascot-art {
    position: absolute;
    left: 0;
    top: 80px;
    width: 205px;
    height: 140px;
  }
  .contact-block {
    position: absolute;
    left: 218px;
    top: 66px;
    right: 16px;
    padding-left: 14px;
    border-left: 1px solid var(--rule);
    color: var(--text-soft);
  }
  .contact-name {
    color: var(--brand-red);
    font-weight: 600;
    font-size: 19px;
    letter-spacing: 0.2px;
    margin-bottom: 10px;
  }
  .contact-address {
    font-size: 13px;
    line-height: 1.45;
    margin-bottom: 12px;
  }
  .contact-lines {
    list-style: none;
    font-size: 13px;
    line-height: 1.5;
  }
  .contact-lines li {
    display: flex;
    align-items: center;
    gap: 8px;
    white-space: nowrap;
  }
  .contact-lines svg {
    width: 10px;
    height: 10px;
    flex: none;
    fill: var(--brand-red);
  }
  /* Back: company name */
  .card-back {
    display: flex;
    align-items: center;
    justify-content: center;
  }
  .company-name {
    color: var(--brand-red);
    font-weight: 700;
    font-size: 46px;
    letter-spacing: -0.5px;
  }
</style>
</head>
<body>
  <main class="card-set">
    <section class="card card-front">
      <svg class="mascot-art" viewBox="0 0 205 140" role="img" aria-label="Charging buffalo mascot illustration with red speed streaks">
        <defs>
          <linearGradient id="mascotTone" x1="0" y1="0" x2="1" y2="0">
            <stop offset="0" stop-color="#ec1f27" stop-opacity="0.85"/>
            <stop offset="0.45" stop-color="#0655a3" stop-opacity="0.9"/>
            <stop offset="1" stop-color="#0a3f7a" stop-opacity="0.95"/>
          </linearGradient>
        </defs>
        <rect x="0" y="0" width="205" height="140" rx="40" fill="url(#mascotTone)"/>
      </svg>

      <div class="contact-block">
        <p class="contact-name">Marcus Whitfield</p>
        <p class="contact-address">4117 W. Larkin Ave.<br>Pharr, TX 78590</p>
        <ul class="contact-lines">
          <li>
            <svg viewBox="0 0 10 10"><path d="M2 0.5 L3.6 0.5 L4.3 2.6 L3.2 3.4 Q4.1 5.6 6.6 6.8 L7.4 5.7 L9.5 6.4 L9.5 8 Q9.5 9.5 8 9.5 Q1 9 0.5 2 Q0.5 0.5 2 0.5 Z"/></svg>
            1-855-317-6094
          </li>
          <li>
            <svg viewBox="0 0 10 10"><path d="M2.5 0 H7.5 Q8.3 0 8.3 0.8 V9.2 Q8.3 10 7.5 10 H2.5 Q1.7 10 1.7 9.2 V0.8 Q1.7 0 2.5 0 Z M2.8 1.2 V7.8 H7.2 V1.2 Z"/></svg>
            (956)238-7160
          </li>
          <li>
            <svg viewBox="0 0 10 10"><path d="M0 2 H10 V8.5 H0 Z M0.6 2.4 L5 5.8 L9.4 2.4 Z" fill-rule="evenodd"/></svg>
            marcuswhitfield@heronhaulage.example
          </li>
          <li>
            <svg viewBox="0 0 10 10"><circle cx="5" cy="5" r="5"/></svg>
            www.heronhaulage.example
          </li>
        </ul>
      </div>
    </section>

    <section class="card card-back">
      <p class="company-name">Heron Haulage</p>
    </section>
  </main>
</body>
</html>
```